We need a complete design for our construction company KELTO CONSTRUCTION based in Auckland New Zealand, we need a logo, website, business card, vehicle design etc..
We are a mid to high-end construction company who work mostly on residential projects and some commercial.

What we want to see in the design;
Professional,
Architectural,
Simple,
Alternative,

We want the design to communicate professionalism, high quality wormanship and and quality service.

Target Market(s)

People looking for a quality building/ construction company

Industry/Entity Type

Construction Company

Contact Information for Business Card

KELTO CONSTRUCTION.co.nz
Lino Verasek
lino@keltoconstruction.example.nz
021 5807 462

Logo Text

KELTO CONSTRUCTION

Number of Pages Required

5+ page

Font styles to use
Sans Serif

Colors

Designer to choose colors to be used in the design.

Requirements
Must have
• Must appear high end, professional, quality, be simple, easy to use, give security to potential clients
Nice to have
• high-quality photos of our recent projects
• about us page
• blog page
• contact us page
• high quality content
Should not have
• should not be hard to use and have too much going on.

```html
<!DOCTYPE html>
<html lang="en">
<head>
<meta charset="utf-8">
<title>Kelto Construction</title>
<link href="https://fonts.googleapis.com/css2?family=Oswald:wght@500;600&family=Open+Sans:wght@400;600;700&family=Roboto:wght@400;500;700&family=Lato:wght@400;700&display=swap" rel="stylesheet">
<style>
:root{
  --blue:#14a0e6;
  --blue-dark:#0d86c4;
  --ink:#222;
  --text:#555;
  --muted:#777;
  --grey-bg:#f3f3f3;
  --footer:#232323;
  --white:#fff;
}
*{box-sizing:border-box;margin:0;padding:0}
html,body{width:1200px;height:3030px;overflow:hidden;background:var(--white)}
body{position:relative;font-family:'Open Sans',sans-serif;color:var(--text)}
.abs{position:absolute}

/* header */
.brand{position:absolute;display:flex;align-items:center;gap:10px;font-family:'Roboto',sans-serif;font-weight:700;letter-spacing:.3px;white-space:nowrap}
.brand-square{width:24px;height:24px;background:var(--blue);flex:none}
.site-header .brand{left:100px;top:64px;font-size:24px;color:var(--ink)}
.top-contact{position:absolute;top:22px;display:flex;align-items:center;gap:10px;font-family:'Roboto',sans-serif;font-size:15px;white-space:nowrap}
.top-contact .dot{width:30px;height:30px;border-radius:50%;display:flex;align-items:center;justify-content:center;flex:none}
.top-email{left:596px;color:var(--blue)}
.top-email .dot{background:var(--blue)}
.top-phone{left:950px;color:var(--ink)}
.top-phone .dot{background:#333}
.main-nav{position:absolute;left:455px;top:77px;width:745px;height:53px;background:var(--blue);clip-path:polygon(36px 0,100% 0,100% 100%,0 100%)}
.main-nav ul{list-style:none;display:flex;position:absolute;left:78px;top:0;height:53px;align-items:center}
.main-nav li{font-family:'Roboto',sans-serif;font-weight:500;font-size:16px;color:var(--white);margin-right:50px}

/* hero */
.hero{position:absolute;left:0;top:130px;width:1200px;height:540px;background:linear-gradient(180deg,#4b5257 0%,#3a4045 45%,#2b2f33 100%)}
.hero::after{content:"";position:absolute;inset:0;background:rgba(0,0,0,.25)}
.hero-content{position:absolute;z-index:2;left:0;width:1200px;text-align:center;color:var(--white)}
.hero h1{font-family:'Oswald',sans-serif;font-weight:600;font-size:62px;letter-spacing:1px;position:absolute;top:100px;width:100%}
.hero p{position:absolute;top:203px;left:225px;width:750px;font-size:16px;line-height:30px;font-weight:600}
.btn-read{position:absolute;top:304px;left:535px;width:130px;height:55px;background:var(--blue);border:2px solid var(--white);color:var(--white);font-family:'Roboto',sans-serif;font-weight:500;font-size:17px;display:flex;align-items:center;justify-content:center}
.hero-arrow{position:absolute;top:240px;z-index:2}

/* feature cards */
.feature{position:absolute;top:576px;width:334px;color:var(--white);padding:24px 18px 0 17px}
.feature h3{font-family:'Roboto',sans-serif;font-weight:700;font-size:20px;margin-bottom:14px}
.feature p{font-size:12.5px;line-height:19px;text-align:justify}
.feature .ph{position:absolute;left:17px;top:145px;width:301px;height:242px}
.feature-blue{background:var(--blue);height:395px}
.feature-left{left:99px;clip-path:polygon(0 0,100% 0,100% 100%,0 93%)}
.feature-right{left:767px;clip-path:polygon(0 0,100% 0,100% 93%,0 100%)}
.feature-dark{left:433px;height:414px;background:#1f2326}
.feature-shadow{position:absolute;top:975px;left:140px;width:920px;height:30px;border-radius:50%;background:radial-gradient(ellipse at center,rgba(0,0,0,.18),rgba(0,0,0,0) 70%)}

/* section headings */
.section-title{position:absolute;left:0;width:1200px;text-align:center;font-family:'Oswald',sans-serif;font-weight:500;font-size:31px;color:var(--blue)}
.title-rule{position:absolute;height:2px;width:70px;background:var(--blue)}

/* about */
.about-text{position:absolute;top:1136px;left:150px;width:900px;text-align:center;font-size:13.5px;line-height:24px;color:#444}
.stat{position:absolute;top:1240px;width:200px;text-align:center;font-family:'Roboto',sans-serif}
.icon-box{height:50px;display:flex;align-items:flex-end;justify-content:center}
.stat .label{margin-top:18px;font-size:15px;font-weight:500}
.stat .value{margin-top:6px;font-size:21px;font-weight:500}
.stat.blue .label,.stat.blue .value{color:var(--blue)}
.stat.dark .label,.stat.dark .value{color:var(--ink)}
.stat-divider{position:absolute;top:1270px;width:1px;height:76px;background:#ccc}

/* services */
.services-photo{position:absolute;left:0;top:1452px;width:564px;height:532px;background:linear-gradient(160deg,#8e7665 0%,#a98b72 35%,#6f5a4c 70%,#4d4038 100%)}
.services-panel{position:absolute;left:564px;top:1452px;width:636px;height:532px;background:var(--grey-bg)}
.services-intro{position:absolute;left:626px;top:1558px;width:480px;font-size:13.5px;line-height:24px;color:#555}
.service{position:absolute;width:225px;font-family:'Roboto',sans-serif}
.service .icon-box{justify-content:flex-start}
.service h4{font-size:16.5px;font-weight:500;color:var(--ink);margin-top:10px}
.service p{font-size:12.5px;line-height:22px;color:#666;margin-top:6px;text-align:justify}

/* projects */
.project{position:absolute;background:var(--white);border:2px solid #ddd;box-shadow:0 2px 6px rgba(0,0,0,.08)}
.project .ph{position:absolute;left:0;top:0;width:100%}
.project .caption{position:absolute;left:0;bottom:0;width:100%;text-align:center;font-family:'Lato',sans-serif;color:var(--ink)}

/* footer */
.site-footer{position:absolute;left:0;top:2608px;width:1200px;height:422px;background:var(--footer);color:var(--white);font-family:'Roboto',sans-serif}
.site-footer .brand{left:100px;top:150px;font-size:18px;color:var(--white);gap:8px}
.site-footer .brand-square{width:20px;height:20px}
.f-head{position:absolute;font-size:16px;font-weight:500;letter-spacing:.5px}
.f-rule{position:absolute;height:1px;background:#777}
.f-links{position:absolute;left:364px;top:126px;list-style:none;font-size:15px;line-height:31px}
.f-links li::before{content:">";margin-right:12px}
.contact-item{position:absolute;left:539px;display:flex;gap:16px}
.contact-item .ring{width:38px;height:38px;border:2px solid var(--white);border-radius:50%;display:flex;align-items:center;justify-content:center;flex:none}
.contact-item strong{display:block;font-size:15px;font-weight:500;letter-spacing:.3px}
.contact-item span{display:block;font-size:12.5px;line-height:21px;color:#ddd;margin-top:4px}
.field{position:absolute;border:1px solid #ccc;border-radius:3px;font-size:11px;color:#ddd;padding:8px 10px}
.btn-send{position:absolute;left:814px;top:246px;width:119px;height:37px;background:var(--blue);border:2px solid var(--white);border-radius:3px;font-size:11.5px;display:flex;align-items:center;justify-content:center}
.f-bottom-rule{position:absolute;left:99px;top:345px;width:1002px;height:1px;background:#ddd}
.copyright{position:absolute;left:0;top:376px;width:1200px;text-align:center;font-size:15px;font-weight:500}
</style>
</head>
<body>

<header class="site-header">
  <div class="brand"><span class="brand-square"></span>KELTO CONSTRUCTION</div>
  <div class="top-contact top-email">
    <span class="dot"><svg width="16" height="12" viewBox="0 0 16 12"><rect x="1" y="1" width="14" height="10" rx="1" fill="none" stroke="#fff" stroke-width="1.6"/><path d="M1 1l7 6 7-6" fill="none" stroke="#fff" stroke-width="1.6"/></svg></span>
    info@keltoconstruction.example.com
  </div>
  <div class="top-contact top-phone">
    <span class="dot"><svg width="14" height="14" viewBox="0 0 24 24"><path d="M6.6 10.8a15 15 0 006.6 6.6l2.2-2.2a1 1 0 011-.25 11.4 11.4 0 003.6.6 1 1 0 011 1V20a1 1 0 01-1 1A17 17 0 013 4a1 1 0 011-1h3.5a1 1 0 011 1c0 1.25.2 2.45.6 3.6a1 1 0 01-.25 1z" fill="#fff"/></svg></span>
    +180 555 0147
  </div>
  <nav class="main-nav"><ul><li>HOME</li><li>ABOUT US</li><li>PROJECTS</li><li>BLOG</li><li>CONTACT US</li></ul></nav>
</header>

<section class="hero" role="img" aria-label="Aerial photo of a building under construction with tower cranes">
  <svg class="hero-arrow" style="left:32px" width="34" height="62" viewBox="0 0 34 62"><path d="M31 2L3 31l28 29" fill="none" stroke="#fff" stroke-width="2.5"/></svg>
  <svg class="hero-arrow" style="left:1134px" width="34" height="62" viewBox="0 0 34 62"><path d="M3 2l28 29L3 60" fill="none" stroke="#fff" stroke-width="2.5"/></svg>
  <div class="hero-content">
    <h1>KELTO CONSTRUCTION</h1>
    <p>We are a mid to high-end construction company who work mostly on residential projects and some commercial.</p>
    <div class="btn-read">READ MORE</div>
  </div>
</section>

<div class="feature-shadow"></div>
<article class="feature feature-blue feature-left">
  <h3>Residential Projects</h3>
  <p>Nemo enim ipsam voluptatem quia voluptas sit aspernatur aut odit aut fugit, sed quia consequuntur magni dolores.</p>
  <div class="ph" role="img" aria-label="Timber house frame under construction" style="background:linear-gradient(180deg,#6fa6d6 0%,#a9c8e0 45%,#c79a5e 60%,#8a6a40 100%)"></div>
</article>
<article class="feature feature-dark">
  <h3>Commercial Projects</h3>
  <p>Nemo enim ipsam voluptatem quia voluptas sit aspernatur aut odit aut fugit, sed quia consequuntur magni dolores.</p>
  <div class="ph" role="img" aria-label="Rolled blueprints on a desk with a city skyline behind" style="background:linear-gradient(180deg,#9fb3c4 0%,#c9d3db 45%,#e8ecef 65%,#8e9aa4 100%)"></div>
</article>
<article class="feature feature-blue feature-right">
  <h3>Full Project Management</h3>
  <p>Nemo enim ipsam voluptatem quia voluptas sit aspernatur aut odit aut fugit, sed quia consequuntur magni dolores.</p>
  <div class="ph" role="img" aria-label="Two builders in hard hats reviewing plans on site" style="background:linear-gradient(160deg,#d8c8b0 0%,#b08f6d 40%,#5f6b7a 70%,#c9b59a 100%)"></div>
</article>

<!-- about -->
<h2 class="section-title" style="top:1076px">ABOUT KELTO CONSTRUCTION</h2>
<p class="about-text">Neque porro quisquam est, qui dolorem ipsum quia dolor sit amet, consectetur, adipisci velit, sed quia non numquam eius modi tempora incidunt ut labore et dolore magnam aliquam quaerat voluptatem.</p>

<div class="stat blue" style="left:60px">
  <div class="icon-box"><svg width="62" height="44" viewBox="0 0 62 44"><rect x="4" y="6" width="54" height="16" rx="3" fill="none" stroke="#14a0e6" stroke-width="3"/><rect x="10" y="12" width="16" height="8" rx="2" fill="#14a0e6"/><rect x="36" y="12" width="16" height="8" rx="2" fill="#14a0e6"/><rect x="2" y="22" width="58" height="14" rx="2" fill="#14a0e6"/><path d="M6 36v6M56 36v6" stroke="#14a0e6" stroke-width="3"/></svg></div>
  <div class="label">BEDROOMS</div><div class="value">3</div>
</div>
<div class="stat-divider" style="left:268px"></div>
<div class="stat dark" style="left:272px">
  <div class="icon-box"><svg width="54" height="48" viewBox="0 0 54 48"><rect x="3" y="3" width="34" height="42" fill="none" stroke="#222" stroke-width="2.5"/><path d="M3 17h34M3 31h34M17 3v42M27 3v42" stroke="#222" stroke-width="1.5"/><path d="M51 45H29l22-22z" fill="#222"/></svg></div>
  <div class="label">SQUARE FEET</div><div class="value">2520</div>
</div>
<div class="stat-divider" style="left:482px"></div>
<div class="stat blue" style="left:496px">
  <div class="icon-box"><svg width="50" height="46" viewBox="0 0 50 46"><path d="M10 20V7a5 5 0 0110 0" fill="none" stroke="#14a0e6" stroke-width="2.5"/><path d="M3 20h44v8a12 12 0 01-12 12H15A12 12 0 013 28z" fill="none" stroke="#14a0e6" stroke-width="3"/><path d="M12 40l-3 5M38 40l3 5" stroke="#14a0e6" stroke-width="2.5"/></svg></div>
  <div class="label">BATHS</div><div class="value">2</div>
</div>
<div class="stat-divider" style="left:704px"></div>
<div class="stat dark" style="left:708px">
  <div class="icon-box"><svg width="46" height="46" viewBox="0 0 46 46"><rect x="3" y="7" width="40" height="36" rx="2" fill="none" stroke="#222" stroke-width="3"/><rect x="3" y="7" width="40" height="9" fill="#222"/><path d="M13 2v9M33 2v9" stroke="#222" stroke-width="3"/><g fill="#222"><rect x="9" y="21" width="6" height="5"/><rect x="20" y="21" width="6" height="5"/><rect x="31" y="21" width="6" height="5"/><rect x="9" y="31" width="6" height="5"/><rect x="20" y="31" width="6" height="5"/><rect x="31" y="31" width="6" height="5"/></g></svg></div>
  <div class="label">YEAR BUILD</div><div class="value">2016</div>
</div>
<div class="stat-divider" style="left:918px"></div>
<div class="stat blue" style="left:930px">
  <div class="icon-box"><svg width="46" height="46" viewBox="0 0 46 46"><path d="M3 18L23 3l20 15" fill="none" stroke="#14a0e6" stroke-width="3"/><path d="M11 30l3-8h18l3 8z" fill="#14a0e6"/><rect x="8" y="29" width="30" height="9" rx="2" fill="#14a0e6"/><circle cx="14" cy="40" r="3" fill="#14a0e6"/><circle cx="32" cy="40" r="3" fill="#14a0e6"/></svg></div>
  <div class="label">CAR PARKING</div><div class="value">1</div>
</div>

<!-- services -->
<div class="services-photo" role="img" aria-label="Smiling builder in hard hat and high-visibility vest in front of brick walls and scaffolding"></div>
<section class="services-panel"></section>
<h2 class="abs" style="left:626px;top:1490px;font-family:'Oswald',sans-serif;font-weight:500;font-size:29px;color:var(--blue)">OUR SERVICES</h2>
<div class="title-rule" style="left:626px;top:1538px"></div>
<p class="services-intro">Sed ut perspiciatis unde omnis iste natus error sit voluptatem accusantium do loremque laudantium.</p>

<div class="service" style="left:626px;top:1632px">
  <div class="icon-box"><svg width="46" height="50" viewBox="0 0 46 50"><path d="M16 4h14l-4 8h-6z" fill="#14a0e6"/><path d="M20 12h6c9 6 14 14 14 22 0 7-7 10-17 10S6 41 6 34c0-8 5-16 14-22z" fill="#14a0e6"/><path d="M2 44h42" stroke="#14a0e6" stroke-width="3"/><text x="23" y="35" font-family="Roboto,sans-serif" font-size="15" font-weight="700" fill="#fff" text-anchor="middle">£</text></svg></div>
  <h4>Residential House</h4>
  <p>Nemo enim ipsam voluptatem quia voluptas sit aspernatur.</p>
</div>
<div class="service" style="left:883px;top:1632px">
  <div class="icon-box"><svg width="52" height="50" viewBox="0 0 52 50"><g fill="#14a0e6"><rect x="4" y="36" width="7" height="10"/><rect x="15" y="30" width="7" height="16"/><rect x="26" y="24" width="7" height="22"/><rect x="37" y="16" width="7" height="30"/></g><path d="M4 28L40 6" stroke="#14a0e6" stroke-width="3"/><path d="M34 4h10v10" fill="none" stroke="#14a0e6" stroke-width="3"/></svg></div>
  <h4>Light Commercial</h4>
  <p>Nemo enim ipsam voluptatem quia voluptas sit aspernatur.</p>
</div>
<div class="service" style="left:626px;top:1800px">
  <div class="icon-box"><svg width="54" height="46" viewBox="0 0 54 46"><rect x="8" y="6" width="38" height="28" rx="2" fill="none" stroke="#14a0e6" stroke-width="3"/><path d="M2 38h50v3H2z" fill="#14a0e6"/><path d="M17 24l10-8 10 8M20 22v7h14v-7" fill="none" stroke="#14a0e6" stroke-width="2.5"/></svg></div>
  <h4>Model Project</h4>
  <p>Nemo enim ipsam voluptatem quia voluptas sit aspernatur.</p>
</div>
<div class="service" style="left:883px;top:1800px">
  <div class="icon-box"><svg width="46" height="50" viewBox="0 0 46 50"><path d="M3 20L23 4l20 16" fill="none" stroke="#14a0e6" stroke-width="3"/><path d="M8 17v29h30V17" fill="none" stroke="#14a0e6" stroke-width="3"/><circle cx="23" cy="30" r="9" fill="none" stroke="#14a0e6" stroke-width="2.5"/><text x="23" y="35" font-family="Roboto,sans-serif" font-size="13" font-weight="700" fill="#14a0e6" text-anchor="middle">$</text></svg></div>
  <h4>Construction Cost</h4>
  <p>Nemo enim ipsam voluptatem quia voluptas sit aspernatur.</p>
</div>

<!-- projects -->
<h2 class="section-title" style="top:2044px">OUR RECENT PROJECTS</h2>
<div class="title-rule" style="left:565px;top:2103px"></div>

<article class="project" style="left:99px;top:2192px;width:315px;height:290px">
  <div class="ph" role="img" aria-label="Steel frame and tower crane against blue sky" style="height:230px;background:linear-gradient(180deg,#3f86c9 0%,#7db1dd 55%,#b9a27e 80%,#7c6d58 100%)"></div>
  <div class="caption" style="height:58px;line-height:56px;font-size:21px;font-weight:700">Commercial Projects</div>
</article>
<article class="project" style="left:787px;top:2192px;width:315px;height:290px">
  <div class="ph" role="img" aria-label="Model roof frame with figurines on building plans" style="height:230px;background:linear-gradient(160deg,#9aa9ba 0%,#c6b49a 40%,#a8834f 70%,#dfe5ea 100%)"></div>
  <div class="caption" style="height:58px;line-height:56px;font-size:21px;font-weight:700">Residential Projects</div>
</article>
<article class="project" style="left:411px;top:2165px;width:380px;height:344px">
  <div class="ph" role="img" aria-label="Modern timber-framed building under a cloudy sky" style="height:272px;background:linear-gradient(180deg,#8f99a3 0%,#b8bec4 35%,#8c6a4c 65%,#5b4637 100%)"></div>
  <div class="caption" style="height:70px;line-height:68px;font-size:24px;font-weight:400">Kelto Construction</div>
</article>

<!-- footer -->
<footer class="site-footer">
  <div class="brand"><span class="brand-square"></span>KELTO CONSTRUCTION</div>

  <div class="f-head" style="left:364px;top:72px">USEFUL LINKS</div>
  <div class="f-rule" style="left:364px;top:102px;width:120px"></div>
  <ul class="f-links"><li>Home</li><li>About us</li><li>Projects</li><li>Blog</li><li>Contact Us</li></ul>

  <div class="f-head" style="left:539px;top:72px">CONTACT US</div>
  <div class="f-rule" style="left:539px;top:102px;width:110px"></div>
  <div class="contact-item" style="top:136px">
    <span class="ring"><svg width="14" height="18" viewBox="0 0 14 18"><path d="M7 1a6 6 0 016 6c0 4.5-6 10-6 10S1 11.5 1 7a6 6 0 016-6z" fill="#fff"/><circle cx="7" cy="7" r="2.2" fill="#232323"/></svg></span>
    <div><strong>ADDRESS,</strong><span>48 Harbour Lane, CT<br>HUB 4, UK</span></div>
  </div>
  <div class="contact-item" style="top:212px">
    <span class="ring"><svg width="10" height="16" viewBox="0 0 10 16"><rect x="1" y="1" width="8" height="14" rx="1.5" fill="none" stroke="#fff" stroke-width="1.6"/><circle cx="5" cy="12" r="1" fill="#fff"/></svg></span>
    <div><strong>PHONE NUMBER:</strong><span>180 555 0147</span></div>
  </div>
  <div class="contact-item" style="top:273px">
    <span class="ring"><svg width="14" height="11" viewBox="0 0 14 11"><rect x="0" y="0" width="14" height="11" rx="1" fill="#fff"/><path d="M0 0l7 6 7-6" fill="none" stroke="#232323" stroke-width="1.4"/></svg></span>
    <div><strong>EMAIL:</strong><span>info@keltoconstruction.example.com</span></div>
  </div>

  <div class="f-head" style="left:814px;top:68px">CONTACT FORM</div>
  <div class="f-rule" style="left:814px;top:98px;width:120px"></div>
  <div class="field" style="left:814px;top:121px;width:138px;height:35px">Name</div>
  <div class="field" style="left:963px;top:121px;width:138px;height:35px">Phone</div>
  <div class="field" style="left:814px;top:165px;width:287px;height:63px">Message</div>
  <div class="btn-send">SEND MESSAGE</div>

  <div class="f-bottom-rule"></div>
  <p class="copyright">Copyrights @ 2018 Kelto Construction. All Rights Reserved.</p>
</footer>

</body>
</html>
```